Exclusive beauty salon needs a price list or services booklet

I need a new very attractive flyer for my beauty salon, containing information on the different services and their prices.
In attachment you can find a pdf of the "old" one, but I'd love to have a beautifully designed new one!
I'd love to have a booklet in format 148 x 148 mm, or in US format, containing 12 or 16 pages, but if you can offer other nice looking designs they are welcome!
The services that need to come in the booklet with their prices can all be found on my website: www.atelierverano.be, starting with
Gelaatsverzorging
Wimperverlenging
Suikerontharing
Wimperlifting
Permanente Make Up
Airbrush Tanning

Target Market(s)

woman from 20 to 89 years old

Industry/Entity Type

Beauty Salon

Font styles to use
Sans Serif

Colors

Designer to choose colors to be used in the design.

Requirements
Must have
• a classy nice look, it must contain details about the services from my beauty salon and their prices, and nice pictures.
• The Names, prices and explanations of the services can easily be found on my website: www.atelierverano.be
Nice to have
• In attachment you can find the "old" price list in pdf, what I need now is a "new booklet" with the new logo and updated services price list.
• I need a very nice and attractive looking booklet, classy chique, Paris chique, looking very expensive.
Should not have
• Not too much colors, not too curly, but still feminine

```html
<!DOCTYPE html>
<html lang="nl">
<head>
<meta charset="utf-8">
<title>Atelier Verano – booklet covers</title>
<link rel="stylesheet" href="https://fonts.googleapis.com/css2?family=Open+Sans:wght@300;400;600&display=swap">
<style>
  :root {
    --bg: #fbe9ea;
    --pink: #dcaab1;
    --blush: #f4eeee;
    --mist: #e7dfe0;
    --charcoal: #555557;
    --ink: #3d3d3f;
    --white: #ffffff;
  }
  * { margin: 0; padding: 0; box-sizing: border-box; }
  html, body { width: 1200px; height: 813px; overflow: hidden; background: var(--bg); }
  body { font-family: "Open Sans", sans-serif; color: var(--ink); }
  .spread {
    position: absolute; left: 50px; top: 131px;
    width: 1100px; height: 550px; display: flex;
    box-shadow: 0 10px 30px rgba(120, 70, 80, .18);
  }
  .page { position: relative; width: 550px; height: 550px; overflow: hidden; }
  .page svg.shapes { position: absolute; inset: 0; }
  .page > *:not(svg) { position: absolute; }

  /* back cover */
  .testimonials-title {
    top: 36px; left: 0; width: 430px; text-align: center;
    font-size: 32px; font-weight: 600; letter-spacing: 1px; color: var(--ink);
  }
  .quote {
    left: 10px; width: 420px; text-align: center;
    font-size: 12px; line-height: 1.25; text-transform: uppercase; color: var(--ink);
  }
  .quote-one { top: 84px; }
  .quote-two { top: 174px; }
  .author {
    left: 0; width: 430px; text-align: center;
    font-size: 18px; line-height: 30px; text-transform: uppercase; letter-spacing: .5px; color: var(--ink);
  }
  .author-one { top: 130px; }
  .author-two { top: 196px; }
  .contact {
    left: 150px; top: 402px; width: 250px; text-align: center;
    font-size: 14px; font-style: normal; line-height: 1.3; color: var(--white);
  }
  .website {
    left: 0; bottom: 14px; width: 550px; text-align: center;
    font-size: 17px; font-weight: 600; letter-spacing: 7px; color: var(--ink);
  }

  /* front cover */
  .brand {
    left: 10px; top: 100px; width: 230px; text-align: center;
    font-size: 14px; letter-spacing: 5px; color: var(--ink);
  }
  .brand::before {
    content: ""; display: block; width: 12px; height: 12px; margin: 0 auto 12px;
    background: var(--charcoal);
  }
  .since { left: 50px; top: 222px; color: var(--white); line-height: 1; }
  .since small { display: block; font-size: 20px; font-weight: 300; margin-left: 26px; }
  .since strong { display: block; font-size: 46px; font-weight: 400; }
  .headline {
    left: 110px; top: 330px; width: 310px; text-align: right;
    font-weight: 300; color: var(--ink); line-height: 1;
  }
  .headline .lead { display: block; font-size: 24px; margin-right: 40px; }
  .headline .big { display: block; font-size: 40px; }
  .headline .small { font-size: 22px; }
</style>
</head>
<body>
<main class="spread">

  <section class="page back-cover">
    <svg class="shapes" width="550" height="550" viewBox="0 0 550 550">
      <rect width="550" height="550" fill="var(--mist)" role="img" aria-label="Faint palm leaf backdrop"/>
      <path d="M0 0 H470 C500 150 420 290 210 300 C120 304 50 290 0 270 Z" fill="var(--pink)"/>
      <path d="M470 0 C500 150 420 290 210 300 C120 304 50 290 0 270" fill="none" stroke="var(--ink)" stroke-width="7"/>
      <rect x="0" y="130" width="470" height="30" fill="var(--blush)"/>
      <rect x="0" y="196" width="450" height="30" fill="var(--blush)"/>
      <ellipse cx="275" cy="440" rx="150" ry="70" fill="var(--charcoal)"/>
      <rect x="0" y="488" width="550" height="62" fill="var(--pink)"/>
    </svg>
    <h2 class="testimonials-title">TESTIMONIALS</h2>
    <p class="quote quote-one">“Ik ben al jaren klant bij Marie en wordt nog steeds met hetzelfde enthousiasme ontvangen. Ik kom altijd helemaal zen buiten!”</p>
    <p class="author author-one">Sofie / Zelfstandige / Eeklo</p>
    <p class="quote quote-two">“Super blij met mijn wimpertjes!”</p>
    <p class="author author-two">Lotte / Directieassistente / Adegem</p>
    <address class="contact">
      Tel: 0471 38 52 19<br>
      Lindenlaan 14 (2e verdieping)<br>
      Rozenhof 9900 EEKLO<br>
      marie@atelierverano.be
    </address>
    <p class="website">www.atelierverano.be</p>
  </section>

  <section class="page front-cover">
    <svg class="shapes" width="550" height="550" viewBox="0 0 550 550">
      <defs>
        <linearGradient id="photo-tones" x1="0" y1="0" x2="1" y2="1">
          <stop offset="0" stop-color="#c99aa3"/>
          <stop offset=".5" stop-color="#efd3c9"/>
          <stop offset="1" stop-color="#e3b8b8"/>
        </linearGradient>
      </defs>
      <rect width="550" height="550" fill="url(#photo-tones)" role="img" aria-label="Portrait photo of a woman with dark hair and bare shoulders, eyes closed"/>
      <path d="M0 0 H230 C235 110 280 180 360 215 H0 Z" fill="var(--blush)"/>
      <path d="M230 0 C235 110 280 180 360 215" fill="none" stroke="var(--charcoal)" stroke-width="6"/>
      <path d="M0 215 H360 C330 245 305 275 285 305 H0 Z" fill="var(--charcoal)"/>
      <circle cx="200" cy="820" r="560" fill="var(--pink)"/>
      <circle cx="200" cy="820" r="560" fill="none" stroke="var(--ink)" stroke-width="6"/>
    </svg>
    <p class="brand">ATELIER VERANO</p>
    <p class="since"><small>Sinds</small><strong>2011</strong></p>
    <h1 class="headline">
      <span class="lead">uw favoriete</span>
      <span class="big">Schoonheids</span>
      <span class="big">instituut</span>
      <span class="big"><span class="small">in </span>Eeklo!</span>
    </h1>
  </section>

</main>
</body>
</html>
```